Brookvane Billboard

Please design a billboard using my photos and logos.
For photo of truck please crop the truck itself out and not have the trees / dirt in photo.
Please put " Best Prices in Sevier County"
Please put " 30-yard Dumpsters Starting at 600.00"
Please put " 16-yard Dumpsters Starting at 300.0"
Please put " Delivery and Pickup 7 Days a week"
Billboard size will be 10 ft tall 30 ft wide

```html
<!DOCTYPE html>
<html lang="en">
<head>
<meta charset="UTF-8">
<title>Brookvane Billboard</title>
<link href="https://fonts.googleapis.com/css2?family=Poppins:wght@700;800&display=swap" rel="stylesheet">
<style>
  :root {
    --ink: #0a0a0a;
    --violet: #7e3a98;
    --paper: #ffffff;
    --backdrop: #ececec;
    --truck-light: #d9dadd;
    --truck-dark: #3b2460;
  }
  * { margin: 0; padding: 0; box-sizing: border-box; }
  html, body { width: 911px; height: 1200px; overflow: hidden; }
  body {
    background: var(--backdrop);
    font-family: "Poppins", sans-serif;
    position: relative;
  }
  .billboard {
    position: absolute;
    left: 20px;
    top: 455px;
    width: 871px;
    height: 290px;
    background: var(--paper);
    overflow: hidden;
    box-shadow: 0 8px 18px rgba(0,0,0,0.18);
  }
  .billboard-shapes {
    position: absolute;
    inset: 0;
    width: 100%;
    height: 100%;
  }
  .truck-photo {
    position: absolute;
    left: 460px;
    top: 40px;
    width: 411px;
    height: 250px;
    border-radius: 18px 6px 0 0;
    background: linear-gradient(90deg, var(--truck-light) 0%, #f1f1f3 40%, var(--truck-dark) 62%, #2a1748 100%);
  }
  .brand {
    position: absolute;
    left: 58px;
    top: 22px;
    display: flex;
    align-items: center;
    gap: 10px;
  }
  .brand-dot {
    width: 18px;
    height: 18px;
    border-radius: 50%;
    background: var(--violet);
  }
  .brand-name {
    color: var(--paper);
    font-weight: 800;
    font-size: 34px;
    line-height: 1.02;
    text-transform: uppercase;
    letter-spacing: 0.5px;
  }
  .headline {
    position: absolute;
    left: 22px;
    top: 114px;
    color: var(--paper);
    font-weight: 800;
    text-transform: uppercase;
    line-height: 1;
  }
  .headline-top { display: block; font-size: 39px; letter-spacing: 0.3px; }
  .headline-bottom { display: block; font-size: 52px; margin-top: 2px; letter-spacing: -0.5px; }
  .headline-accent { color: var(--violet); }
  .offers {
    position: absolute;
    left: 22px;
    top: 209px;
    list-style: none;
  }
  .offer {
    display: flex;
    align-items: center;
    gap: 12px;
    height: 25px;
    color: var(--ink);
    font-weight: 700;
    font-size: 15.5px;
    text-transform: uppercase;
  }
  .offer-tick { width: 12px; height: 12px; flex: none; }
</style>
</head>
<body>
  <section class="billboard">
    <svg class="billboard-shapes" viewBox="0 0 1440 480" preserveAspectRatio="none" aria-hidden="true">
      <rect class="panel-ink" x="0" y="0" width="900" height="340" fill="var(--ink)"/>
      <polygon class="stripe-violet" points="690,0 1010,0 1240,480 780,480 900,330 760,0" fill="var(--violet)"/>
      <polygon class="stripe-violet-upper" points="760,0 1010,0 880,170" fill="var(--violet)"/>
      <polygon class="corner-paper" points="1010,0 1440,0 1440,480 1240,480 880,180" fill="var(--paper)"/>
      <polygon class="stripe-ink" points="720,480 790,480 940,330 870,330" fill="var(--ink)"/>
      <rect class="band-paper" x="0" y="340" width="830" height="140" fill="var(--paper)"/>
    </svg>

    <div class="truck-photo" role="img" aria-label="Photo of a white roll-off truck carrying a purple dumpster"></div>

    <div class="brand">
      <span class="brand-dot"></span>
      <span class="brand-name">Brookvane<br>Dumpsters</span>
    </div>

    <h1 class="headline">
      <span class="headline-top">Best Prices in</span>
      <span class="headline-bottom"><span class="headline-accent">Sevier</span> County</span>
    </h1>

    <ul class="offers">
      <li class="offer">
        <svg class="offer-tick" viewBox="0 0 12 12"><path d="M1 6.5 L4.5 10 L11 2" fill="none" stroke="var(--violet)" stroke-width="1.8"/></svg>
        30-Yard Dumpsters Starting at 600.00
      </li>
      <li class="offer">
        <svg class="offer-tick" viewBox="0 0 12 12"><path d="M1 6.5 L4.5 10 L11 2" fill="none" stroke="var(--violet)" stroke-width="1.8"/></svg>
        16-Yard Dumpsters Starting at 300.0
      </li>
      <li class="offer">
        <svg class="offer-tick" viewBox="0 0 12 12"><path d="M1 6.5 L4.5 10 L11 2" fill="none" stroke="var(--violet)" stroke-width="1.8"/></svg>
        Delivery and Pickup 7 Days a Week
      </li>
    </ul>
  </section>
</body>
</html>
```